Business Card Design

We are a commercial real estate brokerage in San Francisco, leasing office buildings downtown.
I would like a clean, elegant look. Simple but powerful .

Industry/Entity Type

Business

Contact Information for Business Card

Derek Holloway
lic# 07258143
415.555.0172
derek@velt-commercial.example
velt-commercial.example

```html
<!DOCTYPE html>
<html lang="en">
<head>
<meta charset="utf-8">
<title>Velt Commercial — Business Card</title>
<link rel="stylesheet" href="https://fonts.googleapis.com/css2?family=Roboto:wght@400;500;700&display=swap">
<style>
  :root {
    --page-bg: #eeece8;
    --card-bg: #ffffff;
    --brand-slate: #7687a5;
    --band-slate: #7a8aa8;
    --mark-grey: #5a5d63;
    --band-text: #ffffff;
  }
  * { margin: 0; padding: 0; box-sizing: border-box; }
  html, body {
    width: 1200px;
    height: 695px;
    overflow: hidden;
  }
  body {
    background: var(--page-bg);
    font-family: "Roboto", Arial, sans-serif;
    position: relative;
  }
  .business-card {
    position: absolute;
    left: 340px;
    top: 195px;
    width: 520px;
    height: 305px;
    background: var(--card-bg);
    box-shadow: 0 1px 3px rgba(0, 0, 0, 0.18);
  }
  .brand {
    position: absolute;
    left: 0;
    right: 0;
    top: 123px;
    display: flex;
    align-items: center;
    justify-content: center;
    gap: 14px;
  }
  .brand-square {
    width: 40px;
    height: 40px;
    background: var(--mark-grey);
  }
  .brand-name {
    color: var(--brand-slate);
    font-weight: 500;
    font-size: 30px;
    letter-spacing: 0.5px;
    text-transform: uppercase;
    line-height: 1;
  }
  .holder {
    position: absolute;
    left: 0;
    right: 0;
    top: 229px;
    text-align: center;
    color: var(--brand-slate);
  }
  .holder-name {
    font-weight: 700;
    font-size: 16px;
    text-transform: uppercase;
    line-height: 20px;
  }
  .holder-licence {
    font-weight: 400;
    font-size: 14px;
    line-height: 20px;
  }
  .contact-band {
    position: absolute;
    left: 0;
    right: 0;
    bottom: 0;
    height: 35px;
    background: var(--band-slate);
    display: flex;
    align-items: center;
    justify-content: center;
    gap: 5px;
    color: var(--band-text);
    font-size: 14px;
  }
  .contact-item {
    display: flex;
    align-items: center;
    gap: 4px;
    white-space: nowrap;
  }
  .contact-icon {
    width: 9px;
    height: 9px;
  }
</style>
</head>
<body>
  <div class="business-card">
    <div class="brand">
      <span class="brand-square" aria-hidden="true"></span>
      <span class="brand-name">Velt Commercial</span>
    </div>

    <div class="holder">
      <p class="holder-name">Derek Holloway</p>
      <p class="holder-licence">lic# 07258143</p>
    </div>

    <div class="contact-band">
      <span class="contact-item">
        <svg class="contact-icon" viewBox="0 0 10 10" aria-hidden="true">
          <circle cx="5" cy="5" r="5" fill="#fff"/>
          <path d="M3.3 2.6l1 .9-.5.8c.4.8.9 1.3 1.7 1.7l.8-.5.9 1-.7.8C4.8 7.1 2.9 5.2 2.6 3.3z" fill="#7a8aa8"/>
        </svg>
        415.555.0172
      </span>
      <span class="contact-item">
        <svg class="contact-icon" viewBox="0 0 10 10" aria-hidden="true">
          <circle cx="5" cy="5" r="5" fill="#fff"/>
          <rect x="2.5" y="3.2" width="5" height="3.6" fill="none" stroke="#7a8aa8" stroke-width="0.8"/>
          <path d="M2.5 3.2L5 5.2 7.5 3.2" fill="none" stroke="#7a8aa8" stroke-width="0.8"/>
        </svg>
        derek@velt-commercial.example
      </span>
      <span class="contact-item">
        <svg class="contact-icon" viewBox="0 0 10 10" aria-hidden="true">
          <circle cx="5" cy="5" r="4.5" fill="none" stroke="#fff" stroke-width="1"/>
          <ellipse cx="5" cy="5" rx="1.8" ry="4.5" fill="none" stroke="#fff" stroke-width="0.7"/>
          <line x1="0.5" y1="5" x2="9.5" y2="5" stroke="#fff" stroke-width="0.7"/>
        </svg>
        velt-commercial.example
      </span>
    </div>
  </div>
</body>
</html>
```